Accountant website

Please design a accountant website for www.fenwaybridgeadvisory.com.au. This site is majorly out of date, and is not supported by modern browsers.

The style should use the reds from the design at dev.fenwaybridgeadvisory.com.au, and should be modern and make use of Slides (large content slides that the user scrolls through on the front page).

The content is largely already on the site, however happy to move some around to suit the modern design as required.

The dev.fenwaybridgeadvisory.com.au was a rough mock up that I have completed that the client is "happy" with the direction, however this needs a lot of polish and finishing touches, and I will accept designs that differ from this, but highly recommend that this is used as a guide.

Ready to be sliced PSD Only - HTML no required.

In all honesty, although I can technically do a lot of this, the polished finished I want for this site has eluded me in a few attempts, and therefore I am looking out there at you much more artistic people to finish (or redesign if required) this site.

Target Market(s)

Higher end Small - Medium Business

Industry/Entity Type

Accountant

Requirements
Must have
• Must use the logo from dev.fenwaybridgeadvisory.com.au use exactly the red colours as defined in this layout. A basic layout PSD (to get the colour etc) and the logo in ai format is attached to this project. Please ignore the SSL warning on the development site.

The final product does NOT have to be the same as shown on dev.fenwaybridgeadvisory.com.au however the red colour scheme must be used. The client DOES want the logo on the RIGHT.

Must have a front landing page design, and a page layout that considers the other page content (at least one separate PSD)
Nice to have
• I really am looking at a slide format for the front page simular to:

http://www.quillo.com/au/
http://www.vaultmoor.com/

The attached photos should be used on the site. Was considering a rotating banner with these images are a watermark background on a solid Red header bar, but happy to be shown other options.
Should not have
• Please no "Layout Goblin" submissions.

```html
<!DOCTYPE html>
<html lang="en">
<head>
<meta charset="utf-8">
<title>Fenway Bridge Advisory</title>
<link rel="stylesheet" href="https://fonts.googleapis.com/css2?family=Roboto:wght@300;400;500;700;900&display=swap">
<style>
  :root{
    --red:#cf1f2e;
    --red-dark:#a8151f;
    --ink:#2b2b2b;
    --muted:#6d6d6d;
    --line:#d4d4d4;
    --paper:#ffffff;
    --footer:#1c1c1c;
    --footer-deep:#0f0f0f;
    --footer-text:#9a9a9a;
  }
  *{box-sizing:border-box;margin:0;padding:0}
  html,body{width:1200px;height:2416px;overflow:hidden}
  body{position:relative;background:var(--paper);font-family:"Roboto",Arial,sans-serif;color:var(--ink)}
  .abs{position:absolute}

  /* header */
  .utility{left:175px;top:12px;display:flex;gap:18px;font-size:11px;color:var(--muted)}
  .utility span{display:flex;align-items:center;gap:5px}
  .utility i{display:inline-block;width:8px;height:8px;background:#9c9c9c;border-radius:1px}
  .main-nav{left:175px;top:42px;display:flex;gap:4px}
  .main-nav a{font-size:13px;font-weight:700;color:var(--ink);text-decoration:none;padding:8px 12px}
  .main-nav a.active{background:var(--red);color:#fff}
  .brand{right:50px;top:26px;display:flex;align-items:center;gap:12px}
  .brand-mark{width:34px;height:34px;background:var(--red)}
  .brand-name{font-size:22px;font-weight:700;color:var(--ink);letter-spacing:.5px;line-height:1}

  /* hero */
  .hero{left:0;top:88px;width:1200px;height:544px;
    background:linear-gradient(100deg,#4a3a32 0%,#6e5a4c 38%,#8c7868 60%,#a39486 100%)}
  .hero-title{left:175px;top:220px;font-size:44px;font-weight:900;color:var(--red);text-transform:uppercase;letter-spacing:.5px}
  .hero-sub{left:175px;top:272px;width:520px;font-size:32px;font-weight:300;color:#fff;line-height:1.15}
  .hero-dots{left:178px;top:466px;display:flex;gap:8px}
  .hero-dots i{width:12px;height:12px;border-radius:50%;border:2px solid #fff;display:block}
  .hero-dots i.on{background:#fff}

  /* timeline */
  .connectors{left:0;top:0;width:1200px;height:2416px}
  .photo-frame{background:#fff;padding:6px;box-shadow:0 2px 8px rgba(0,0,0,.22)}
  .photo{width:100%;height:100%}
  .badge{position:absolute;right:-22px;bottom:-20px;width:52px;height:52px;background:var(--red);
    border:3px solid #fff;display:flex;align-items:center;justify-content:center}
  .block-title{font-size:21px;font-weight:700;color:var(--red);margin-bottom:14px}
  .block p{font-size:12.5px;line-height:1.55;color:var(--muted);margin-bottom:10px}
  .block p strong{color:var(--ink)}

  /* footer */
  .footer{left:0;top:2192px;width:1200px;height:224px;background:var(--footer);border-top:5px solid var(--red)}
  .footer-bottom{left:0;top:2382px;width:1200px;height:34px;background:var(--footer-deep)}
  .footer h4{font-size:18px;font-weight:500;color:#fff;margin-bottom:14px}
  .sitemap{left:175px;top:2222px}
  .sitemap-cols{display:flex;gap:36px}
  .sitemap ul{list-style:none}
  .sitemap li{font-size:11px;color:var(--footer-text);line-height:18px;display:flex;align-items:center;gap:6px}
  .sitemap li::before{content:"";width:4px;height:4px;background:var(--red)}
  .map{left:420px;top:2228px;width:150px;height:120px;background:linear-gradient(135deg,#d9d6cc,#c4c9bd)}
  .contact{left:600px;top:2222px}
  .contact p{font-size:11px;color:var(--footer-text);line-height:18px;display:flex;align-items:center;gap:7px}
  .badges{left:800px;top:2232px;display:flex;gap:12px}
  .badges span{width:92px;height:38px;background:#f2f2f2;border-radius:3px;display:block}
  .copyright{left:800px;top:2290px;width:300px;font-size:11px;color:var(--footer-text);line-height:17px}
</style>
</head>
<body>

<header>
  <div class="abs utility">
    <span><i></i>Login</span><span><i></i>Register</span><span><i></i>Contact Us</span><span><i></i>Testimonials</span>
  </div>
  <nav class="abs main-nav">
    <a href="#">About Us</a><a href="#" class="active">Services</a><a href="#">Working With Us</a><a href="#">Testimonials</a><a href="#">Article Of The Moment</a>
  </nav>
  <div class="abs brand"><span class="brand-mark"></span><span class="brand-name">Fenway Bridge Advisory</span></div>
</header>

<section class="abs hero" role="img" aria-label="Photograph of a smiling accountant in a red top standing in a bright modern office"></section>
<h1 class="abs hero-title">Business can be hard</h1>
<p class="abs hero-sub">But we make detailed analysis of your finance easy.</p>
<div class="abs hero-dots"><i class="on"></i><i></i></div>

<svg class="abs connectors" viewBox="0 0 1200 2416" fill="none" stroke="#d4d4d4" stroke-width="2">
  <path d="M280 852 V870 H860 V884"/>
  <path d="M860 1076 V1150 H280 V1228"/>
  <path d="M280 1440 V1500 H840 V1580"/>
  <path d="M840 1766 V1840 H280 V1920"/>
</svg>

<!-- service blocks -->
<div class="abs photo-frame" style="left:180px;top:640px;width:200px;height:210px">
  <div class="photo" role="img" aria-label="Photo of an accountant at her desk" style="background:linear-gradient(160deg,#d8d2cc,#b34a42)"></div>
  <span class="badge"><svg width="24" height="24" viewBox="0 0 24 24" fill="none" stroke="#fff" stroke-width="2"><circle cx="12" cy="8" r="4"/><path d="M4 21c1-5 15-5 16 0"/></svg></span>
</div>
<div class="abs block" style="left:520px;top:650px;width:560px">
  <h2 class="block-title">Getting to Know Fenway Bridge Advisory</h2>
  <p>Fenway Bridge Advisory aims to service the needs of its clients by focusing on the present rather than reporting on historical figures. We recognise that business owners benefit from regular contact with their accountant. Our team undertakes a hands on approach in working with business owners to improve their business.</p>
</div>

<div class="abs block" style="left:180px;top:912px;width:500px">
  <h2 class="block-title">Believing in the here and now</h2>
  <p>A proactive accountant that focuses on providing timely and relevant information. This means informed decisions can be made, accurate forecasts, industry comparisons, and other key diagnostic tools can be produced to ensure the performance of your business is always tracked and geared towards improvement.</p>
</div>
<div class="abs photo-frame" style="left:720px;top:884px;width:280px;height:192px">
  <div class="photo" role="img" aria-label="Photo of the advisory team seated together at a red office wall" style="background:linear-gradient(180deg,#cf2d32 0%,#c93a3a 50%,#e8e4e0 100%)"></div>
</div>

<div class="abs photo-frame" style="left:180px;top:1228px;width:200px;height:212px">
  <div class="photo" role="img" aria-label="Photo of an accountant on a harbour boardwalk" style="background:linear-gradient(160deg,#a9c2d4,#c24a44)"></div>
  <span class="badge"><svg width="24" height="24" viewBox="0 0 24 24" fill="none" stroke="#fff" stroke-width="2"><rect x="3" y="5" width="18" height="16"/><path d="M3 10h18M8 3v4M16 3v4"/></svg></span>
</div>
<div class="abs block" style="left:520px;top:1262px;width:560px">
  <h2 class="block-title">Monthly billing to plan by</h2>
  <p>Annual fees, agreed upon and broken down into 12 easy monthly instalments. This means no nasty surprises, your accounting budget is planned for the entire year. There are no unexpected bulk bills and it assists with cash flow management.</p>
</div>

<div class="abs block" style="left:180px;top:1582px;width:500px">
  <h2 class="block-title">Your place, in your time</h2>
  <p>Mobile Service. An accountant that delivers! Saving you travel time and stress.</p>
  <p>This means your time can be better spent on achieving your professional and personal goals. Furthermore, all of the required information is at hand, thus enabling efficiency in resolving business matters, and on implementing business improvement measures.</p>
</div>
<div class="abs photo-frame" style="left:720px;top:1580px;width:240px;height:186px">
  <div class="photo" role="img" aria-label="Photo of an accountant in front of a city waterfront" style="background:linear-gradient(160deg,#b9c6cf,#6d6a6c)"></div>
</div>

<div class="abs photo-frame" style="left:180px;top:1920px;width:200px;height:210px">
  <div class="photo" role="img" aria-label="Photo of an accountant answering a phone call" style="background:linear-gradient(160deg,#c8d3da,#c24a44)"></div>
  <span class="badge"><svg width="24" height="24" viewBox="0 0 24 24" fill="#fff"><path d="M6.6 10.8a15 15 0 006.6 6.6l2.2-2.2c.3-.3.7-.4 1-.2 1.1.4 2.3.6 3.6.6.6 0 1 .4 1 1V20c0 .6-.4 1-1 1A17 17 0 013 4c0-.6.4-1 1-1h3.5c.6 0 1 .4 1 1 0 1.3.2 2.5.6 3.6.1.3 0 .7-.2 1z"/></svg></span>
</div>
<div class="abs block" style="left:520px;top:1940px;width:560px">
  <h2 class="block-title">We will actually call you back</h2>
  <p><strong>Responsiveness:</strong> Fenway Bridge Advisory offers a communication guarantee. All correspondence will be responded to within 24 hrs.</p>
  <p>This means no time is wasted waiting on a reply, opportunities can be seized faster and any issues can be resolved before they become a potential business threat. Best of all, most calls are included in the monthly fee, so no watching the clock when we are talking to you.</p>
</div>

<footer>
  <div class="abs footer"></div>
  <div class="abs footer-bottom"></div>
  <div class="abs sitemap">
    <h4>Site Map</h4>
    <div class="sitemap-cols">
      <ul><li>About Us</li><li>Services</li><li>Working With Us</li><li>Testimonials</li><li>Article</li></ul>
      <ul><li>News</li><li>Newsletter</li><li>Articles</li><li>Contact</li><li>Client Login</li></ul>
    </div>
  </div>
  <div class="abs map" role="img" aria-label="Street map showing the office location"></div>
  <div class="abs contact">
    <h4>Contact Us</h4>
    <p><svg width="10" height="12" viewBox="0 0 10 12" fill="var(--red)"><path d="M5 0a4 4 0 00-4 4c0 3 4 8 4 8s4-5 4-8a4 4 0 00-4-4z"/></svg>12 Harbour Rd, Kelvin Grove</p>
    <p style="padding-left:17px">QLD 4059</p>
    <p><svg width="10" height="10" viewBox="0 0 24 24" fill="var(--red)"><path d="M6.6 10.8a15 15 0 006.6 6.6l2.2-2.2c.3-.3.7-.4 1-.2 1.1.4 2.3.6 3.6.6.6 0 1 .4 1 1V20c0 .6-.4 1-1 1A17 17 0 013 4c0-.6.4-1 1-1h3.5c.6 0 1 .4 1 1 0 1.3.2 2.5.6 3.6.1.3 0 .7-.2 1z"/></svg>P: 07 5550 1234</p>
    <p style="padding-left:17px">F: 07 5550 1235</p>
  </div>
  <div class="abs badges"><span></span><span></span></div>
  <p class="abs copyright">Copyright © 2014 Fenway Bridge Advisory.<br>All rights reserved.</p>
</footer>

</body>
</html>
```